Tech business card design

We need an amazing business card design for our new business 'Pexla' a marketing tech startup based in Sydney, Australia. We provide an online marketplace for businesses to search and buy advertising media, connect with service providers and learn more about marketing. We wish to communicate 'cool tech', reliability and professionalism and design based around our logo.

Target Market(s)

Business Owners

Contact Information for Business Card

Name
Position
Email Address
Website
Phone Number

Font styles to use
Other font styles liked:
• Avenir & Avenir Next

Colors

Designer to choose colors to be used in the design.

```html
<!DOCTYPE html>
<html lang="en">
<head>
<meta charset="utf-8">
<title>Pexla – Business Card</title>
<link href="https://fonts.googleapis.com/css2?family=Nunito+Sans:wght@400;700;800&display=swap" rel="stylesheet">
<style>
  :root {
    --bg: #1e1e20;
    --card-dark: #1a1a1b;
    --card-dark-mark: #2a2a2c;
    --card-light: #f4f4f4;
    --navy: #14173d;
    --grey-text: #7a7a7e;
    --rule: #9a9a9c;
  }
  * { margin: 0; padding: 0; box-sizing: border-box; }
  html, body {
    width: 1200px; height: 800px; overflow: hidden;
    background: var(--bg);
    font-family: "Nunito Sans", Arial, sans-serif;
  }
  .stage {
    position: relative; width: 1200px; height: 800px;
  }
  .card {
    position: absolute; left: 340px; width: 520px; height: 297px;
    border-radius: 2px; overflow: hidden;
  }
  .card--back { top: 88px; background: var(--card-dark); }
  .card--front { top: 413px; background: var(--card-light); }

  .back-name {
    position: absolute; left: 70px; top: 62px;
    font-size: 96px; font-weight: 800; letter-spacing: -2px;
    color: var(--card-dark-mark); line-height: 1;
  }

  .front-name {
    position: absolute; right: 58px; top: 20px;
    font-size: 70px; font-weight: 800; letter-spacing: -1.5px;
    color: var(--navy); line-height: 1;
  }
  .rule {
    position: absolute; left: 118px; right: 22px; top: 150px;
    height: 1px; background: var(--rule);
  }
  .person {
    position: absolute; left: 30px; top: 176px;
  }
  .person__name {
    font-size: 17px; font-weight: 700; color: var(--navy);
    letter-spacing: 0.5px; line-height: 1.1;
  }
  .person__role {
    font-size: 14px; color: var(--grey-text); letter-spacing: 0.6px;
  }
  .website {
    position: absolute; right: 22px; top: 180px;
    font-size: 12px; font-weight: 700; color: #4a4a50;
  }
  .contacts {
    position: absolute; left: 30px; top: 226px; list-style: none;
  }
  .contacts li {
    display: flex; align-items: center; gap: 9px;
    font-size: 13px; color: var(--grey-text); height: 21px;
  }
  .contacts svg { width: 12px; height: 12px; flex: none; }
  .band {
    position: absolute; left: 0; right: 0; bottom: 0; height: 7px;
    background: var(--navy);
  }
</style>
</head>
<body>
<main class="stage">
  <section class="card card--back" aria-label="Card back">
    <div class="back-name">Pexla</div>
  </section>

  <section class="card card--front" aria-label="Card front">
    <div class="front-name">Pexla</div>
    <div class="rule"></div>
    <div class="person">
      <div class="person__name">DANIEL REYES</div>
      <div class="person__role">FOUNDER, DIRECTOR</div>
    </div>
    <div class="website">www.pexlamedia.com.au</div>
    <ul class="contacts">
      <li>
        <svg viewBox="0 0 12 12" aria-hidden="true"><rect x="2.5" y="0.5" width="7" height="11" rx="1" fill="none" stroke="#14173d" stroke-width="1.2"/><line x1="5" y1="9.5" x2="7" y2="9.5" stroke="#14173d" stroke-width="1"/></svg>
        +61 (0)400 555 019
      </li>
      <li>
        <svg viewBox="0 0 12 12" aria-hidden="true"><rect x="0.5" y="2" width="11" height="8" fill="#14173d"/><polyline points="0.5,2 6,6.5 11.5,2" fill="none" stroke="#f4f4f4" stroke-width="1"/></svg>
        daniel@pexlamedia.com.au
      </li>
    </ul>
    <div class="band"></div>
  </section>
</main>
</body>
</html>
```